QVR business card

Need a business card for a company that provides instructional design and elearning development services. The website is here: http://quorvane.studio/

I'm attaching a current logo, as well as the old business card design. While I like to keep it clean, the old design is too simplistic for my liking. The only idea I want to reuse from the old design is placing industry jargon on the back of the card, just need a better way to present it. But if you have other ideas for the back--feel free to experiment.

Please use the colors complementary to the color we have on the website. Thank you!

```html
<!DOCTYPE html>
<html lang="en">
<head>
<meta charset="utf-8">
<title>QVR business card</title>
<link rel="stylesheet" href="https://fonts.googleapis.com/css2?family=Open+Sans:wght@300;400;600;700&display=swap">
<style>
  :root {
    --backdrop: #8f9090;
    --paper: #f1f1f3;
    --teal: #1a9e9b;
    --gold: #bdb278;
    --ink: #3a3a3c;
    --rule: #9a9a9c;
    --jargon: #e4eeee;
  }
  * { margin: 0; padding: 0; box-sizing: border-box; }
  html, body {
    width: 1105px; height: 1200px; overflow: hidden;
    background: var(--backdrop);
    font-family: "Open Sans", Arial, sans-serif;
  }
  .card {
    position: absolute; left: 182px;
    width: 747px; height: 427px;
    overflow: hidden;
  }
  .card-front { top: 119px; background: var(--paper); }
  .card-back { top: 638px; background: var(--teal); }

  .brand {
    position: absolute; left: 48px; top: 182px;
    display: flex; align-items: center; gap: 14px;
  }
  .brand-mark { width: 34px; height: 34px; background: var(--teal); }
  .brand-name {
    font-size: 62px; font-weight: 700; line-height: 1;
    color: var(--gold); letter-spacing: 2px;
  }
  .divider {
    position: absolute; left: 359px; top: 134px;
    width: 1px; height: 161px; background: var(--rule);
  }
  .contact { position: absolute; left: 388px; top: 130px; }
  .contact-name { font-size: 23px; font-weight: 600; color: var(--teal); line-height: 1.2; }
  .contact-role { font-size: 18px; color: var(--gold); line-height: 1.3; margin-bottom: 14px; }
  .contact-line {
    display: flex; align-items: center; gap: 10px;
    font-size: 18px; color: var(--ink); height: 29px;
  }
  .contact-line svg { width: 16px; height: 16px; flex: none; }
  .edge-band { position: absolute; left: 0; bottom: 0; width: 747px; height: 19px; }

  .jargon { position: absolute; left: 0; top: 0; }
  .jargon text { fill: var(--jargon); font-family: "Open Sans", Arial, sans-serif; }
  .jargon .term { font-size: 44px; font-weight: 400; }
  .jargon .question { font-size: 56px; font-weight: 600; }
</style>
</head>
<body>
  <section class="card card-front">
    <div class="brand">
      <span class="brand-mark"></span>
      <span class="brand-name">QVR</span>
    </div>
    <div class="divider"></div>
    <div class="contact">
      <p class="contact-name">Adrian Velcourt</p>
      <p class="contact-role">CEO/Founder</p>
      <p class="contact-line">
        <svg viewBox="0 0 16 16"><path fill="#1a9e9b" d="M3.5 1.5l2.5 0 1 3.5-1.8 1.3a9 9 0 0 0 4.5 4.5L11 9l3.5 1v2.5c0 1-1 2-2 2C6.5 14.5 1.5 9.5 1.5 3.5c0-1 1-2 2-2z"/></svg>
        555-010-4827
      </p>
      <p class="contact-line">
        <svg viewBox="0 0 16 16"><rect x="1" y="3" width="14" height="10" fill="#1a9e9b"/><path d="M1.5 3.5L8 9l6.5-5.5" fill="none" stroke="#f1f1f3" stroke-width="1.3"/></svg>
        avelcourt@quorvane.studio
      </p>
      <p class="contact-line">
        <svg viewBox="0 0 16 16"><circle cx="8" cy="8" r="7" fill="#1a9e9b"/><path d="M1 8h14M8 1c-3 3-3 11 0 14M8 1c3 3 3 11 0 14" fill="none" stroke="#f1f1f3" stroke-width="1"/></svg>
        www.quorvane.studio
      </p>
    </div>
    <svg class="edge-band" viewBox="0 0 747 19">
      <polygon points="0,0 488,0 482,19 0,19" fill="var(--teal)"/>
      <polygon points="491,0 747,0 747,19 485,19" fill="var(--gold)"/>
    </svg>
  </section>

  <section class="card card-back">
    <svg class="jargon" width="747" height="427" viewBox="0 0 747 427">
      <text class="term" x="29" y="54" textLength="682" lengthAdjust="spacing">STORYBOARDS ONBOARDING</text>
      <text class="term" x="29" y="102" textLength="682" lengthAdjust="spacing">COMPLIANCE TRAINING UX</text>
      <text class="term" x="29" y="150" textLength="682" lengthAdjust="spacing">ASSESSMENT DESIGN LXP</text>
      <text class="question" x="29" y="218" textLength="682" lengthAdjust="spacing">READY TO TEACH?</text>
      <text class="term" x="29" y="286" textLength="682" lengthAdjust="spacing">VIDEO SCRIPTS ANIMATION</text>
      <text class="term" x="29" y="341" textLength="682" lengthAdjust="spacing">ACCESSIBILITY ROLEPLAY</text>
      <text class="term" x="29" y="399" textLength="682" lengthAdjust="spacing">SIMULATIONS MICROCOURSES</text>
    </svg>
  </section>
</body>
</html>
```